RTavenor Business Cards & Letterhead

I have a logo but need a design for some new business cards. We are a Design-Build Firm that specializes in the design and construction of commercial projects.
the cards need to be professional. no cartoon stuff.
i would like to have the cards in AI format so I can update the card as needed. Logo is provided.
Our Address is: 4187 Marlowe Ct. Corvale, Westmark 27614

```html
<!DOCTYPE html>
<html lang="en">
<head>
<meta charset="utf-8">
<title>RTavenor Business Card</title>
<link rel="stylesheet" href="https://fonts.googleapis.com/css2?family=Open+Sans:wght@400;600;700;800&display=swap">
<style>
  :root {
    --canvas-bg: #e9e7e4;
    --card-bg: #1f1f24;
    --brand-grey: #8a8b90;
    --brand-blue: #1877c4;
    --brand-blue-dark: #0e4f8a;
    --text-white: #f2f2f2;
    --emboss: #121215;
    --pattern-dark: #101013;
    --pattern-light: #6d6e73;
  }
  * { margin: 0; padding: 0; box-sizing: border-box; }
  html, body {
    width: 1200px; height: 780px; overflow: hidden;
    background: var(--canvas-bg);
    font-family: "Open Sans", Arial, sans-serif;
  }
  .canvas {
    width: 1200px; height: 780px;
    display: flex; align-items: center; justify-content: center; gap: 40px;
  }
  .card {
    position: relative;
    width: 540px; height: 309px;
    background: var(--card-bg);
    border-radius: 3px;
    box-shadow: 0 10px 24px rgba(0,0,0,.22);
    overflow: hidden;
  }

  /* Back */
  .card-back__pattern {
    position: absolute; inset: 0;
    background: linear-gradient(135deg, var(--pattern-light) 0%, #2a2a2f 35%, var(--pattern-dark) 70%, #1a1a1e 100%);
  }
  .card-back__brand {
    position: absolute; left: 50%; top: 50%;
    transform: translate(-50%, -50%);
    display: flex; align-items: center; gap: 12px;
  }
  .brand-square { width: 26px; height: 26px; background: var(--brand-blue); }
  .brand-name {
    font-weight: 800; font-size: 40px; letter-spacing: 1px;
    color: var(--brand-grey); line-height: 1;
  }

  /* Front */
  .card-front__brand {
    position: absolute; left: 34px; top: 44px;
    display: flex; align-items: center; gap: 10px;
  }
  .card-front__brand .brand-square { width: 22px; height: 22px; }
  .card-front__brand .brand-name { font-size: 34px; }

  .card-front__side-mark {
    position: absolute; right: 4px; top: 50%;
    transform: translateY(-50%) rotate(180deg);
    writing-mode: vertical-rl;
    font-weight: 800; font-size: 44px; letter-spacing: 1px;
    color: var(--emboss); line-height: 1;
  }

  .contact-block { position: absolute; left: 34px; top: 120px; }
  .contact-block__accent {
    position: absolute; left: 0; top: 4px;
    width: 10px; height: 40px;
    background: linear-gradient(180deg, var(--brand-blue-dark), var(--brand-blue));
  }
  .contact-block__body { padding-left: 22px; }
  .person-name {
    font-weight: 700; font-size: 21px; letter-spacing: .5px;
    color: var(--brand-blue); line-height: 1.05; text-transform: uppercase;
  }
  .person-title {
    font-weight: 600; font-size: 13px; color: var(--text-white); margin-top: 3px;
  }
  .address {
    font-size: 13px; color: var(--text-white); line-height: 1.35;
    margin-top: 12px; font-style: normal;
  }
  .contact-list { list-style: none; margin-top: 10px; }
  .contact-list li {
    display: flex; align-items: center; gap: 8px;
    font-size: 13px; color: var(--text-white); line-height: 1.45;
  }
  .contact-list svg { width: 12px; height: 12px; flex: none; }
</style>
</head>
<body>
<main class="canvas">

  <section class="card card-back" aria-label="Card back">
    <div class="card-back__pattern" role="img" aria-label="Repeating brand monogram pattern fading from grey to black"></div>
    <div class="card-back__brand">
      <span class="brand-square"></span>
      <span class="brand-name">RTAVENOR</span>
    </div>
  </section>

  <section class="card card-front" aria-label="Card front">
    <div class="card-front__brand">
      <span class="brand-square"></span>
      <span class="brand-name">RTAVENOR</span>
    </div>

    <div class="card-front__side-mark" aria-hidden="true">RTAVENOR</div>

    <div class="contact-block">
      <span class="contact-block__accent"></span>
      <div class="contact-block__body">
        <h1 class="person-name">Rowan Tavenor</h1>
        <p class="person-title">Founder/President</p>
        <address class="address">4187 Marlowe Ct. Corvale,<br>Westmark 27614</address>
        <ul class="contact-list">
          <li>
            <svg viewBox="0 0 16 16" aria-hidden="true"><path fill="#1877c4" d="M3.6 1.5l2.2 2.6-1.2 1.6c.9 1.9 2.2 3.2 4.1 4.1l1.6-1.2 2.6 2.2-1.3 2.3C7 13 3 9 1.9 3z"/></svg>
            (555) 210-0148
          </li>
          <li>
            <svg viewBox="0 0 16 16" aria-hidden="true"><circle cx="8" cy="8" r="6.5" fill="none" stroke="#1877c4" stroke-width="1.5"/><ellipse cx="8" cy="8" rx="2.8" ry="6.5" fill="none" stroke="#1877c4" stroke-width="1.2"/><line x1="1.5" y1="8" x2="14.5" y2="8" stroke="#1877c4" stroke-width="1.2"/></svg>
            www.rtavenor.com
          </li>
          <li>
            <svg viewBox="0 0 16 16" aria-hidden="true"><rect x="1.5" y="3.5" width="13" height="9" fill="none" stroke="#1877c4" stroke-width="1.5"/><path d="M1.5 3.5L8 9l6.5-5.5" fill="none" stroke="#1877c4" stroke-width="1.5"/></svg>
            RST@RTavenor.com
          </li>
        </ul>
      </div>
    </div>
  </section>

</main>
</body>
</html>
```